Satchel & Sundial needs new business card design

I need a new business card design. I'm looking for out-of-the-box design which represents the freedom of being a location independent entrepreneur.
I offer coaching, retreats and trips.
I would like to see designs with and without the photo.
Colors I use are black (#000000), green (#25A796) and brown (#D7C38C)
Website satchelandsundial.example

Target Market(s)

location independent entrepreneurs, digital nomads, people looking to swap the 9 to 5 for a lifestyle business

Industry/Entity Type

Business

Contact Information for Business Card

Dorota Falkner
Your Lifestyle Business Coach, Retreat & Trip Leader
http://satchelandsundial.example
hello@satchelandsundial.example
Live a life you don't need a holiday from

Font styles to use
Serif
Sans Serif

Requirements
Must have
• One side should contain only the logo. I would also consider having the "Live a life you don't need a holiday from" on that side too (depending on how it looks)
• Please show both sides on the designs.

```html
<!DOCTYPE html>
<html lang="en">
<head>
<meta charset="utf-8">
<title>Satchel &amp; Sundial – Business Card</title>
<link rel="stylesheet" href="https://fonts.googleapis.com/css2?family=Lato:wght@400;700&display=swap">
<style>
  :root {
    --ink: #000000;
    --card-black: #1e1c1d;
    --teal: #25A796;
    --sand: #D7C38C;
    --sand-light: #e2d3a4;
    --paper-text: #2a2a2a;
    --white: #f4f4f4;
    --stage: #6b6b6b;
  }
  * { box-sizing: border-box; margin: 0; padding: 0; }
  html, body { width: 1200px; height: 950px; overflow: hidden; }
  body {
    background: radial-gradient(ellipse at 40% 35%, #8a8a8a 0%, var(--stage) 60%, #4a4a4a 100%);
    font-family: "Lato", Arial, sans-serif;
    position: relative;
  }
  .card {
    position: absolute;
    width: 560px;
    height: 320px;
    border-radius: 4px;
    box-shadow: 0 14px 30px rgba(0,0,0,0.35);
    overflow: hidden;
  }
  /* Front side */
  .card--front {
    left: 90px; top: 110px;
    background: linear-gradient(135deg, var(--sand-light), var(--sand));
  }
  .front__body {
    position: absolute;
    left: 150px; top: 44px; right: 30px;
    color: var(--paper-text);
  }
  .wordmark {
    font-weight: 700;
    text-transform: uppercase;
    letter-spacing: 1px;
    font-size: 32px;
    line-height: 1;
  }
  .wordmark--dark { color: var(--ink); }
  .wordmark--light { color: var(--white); }
  .holder-name {
    margin-top: 34px;
    color: var(--teal);
    font-weight: 700;
    font-size: 17px;
    letter-spacing: 1.5px;
    text-transform: uppercase;
  }
  .holder-role {
    font-size: 15px;
    line-height: 1.35;
    margin-top: 4px;
  }
  .contact {
    list-style: none;
    margin-top: 14px;
    font-size: 14px;
    line-height: 1.6;
  }
  .contact li { display: flex; align-items: center; gap: 10px; }
  .contact svg { flex: none; }
  .tagline-band {
    position: absolute;
    left: 0; right: 0; bottom: 0;
    height: 54px;
    background: var(--card-black);
    display: flex;
    align-items: center;
    padding-left: 34px;
  }
  .tagline {
    color: var(--teal);
    font-size: 15px;
    letter-spacing: 1.5px;
  }
  /* Back side */
  .card--back {
    left: 560px; top: 520px;
    background: var(--card-black);
  }
  .back__logo {
    position: absolute;
    left: 0; right: 0; top: 0; bottom: 0;
    display: flex;
    align-items: center;
    justify-content: center;
  }
  .social {
    position: absolute;
    left: 36px; top: 50%;
    transform: translateY(-50%);
    display: flex;
    flex-direction: column;
    gap: 6px;
  }
  .social span {
    display: block;
    width: 14px; height: 14px;
    background: var(--teal);
    border-radius: 2px;
  }
</style>
</head>
<body>
  <section class="card card--front" aria-label="Business card front">
    <div class="front__body">
      <p class="wordmark wordmark--dark">Satchel &amp; Sundial</p>
      <p class="holder-name">Dorota Falkner</p>
      <p class="holder-role">Your Lifestyle Business Coach<br>Retreat &amp; Trip Leader</p>
      <ul class="contact">
        <li>
          <svg width="13" height="13" viewBox="0 0 13 13" aria-hidden="true">
            <rect x="0" y="0" width="13" height="13" rx="2" fill="#25A796"/>
            <path d="M2.5 4 L6.5 7 L10.5 4" stroke="#1e1c1d" stroke-width="1.2" fill="none"/>
          </svg>
          hello@satchelandsundial.example
        </li>
        <li>
          <svg width="13" height="13" viewBox="0 0 13 13" aria-hidden="true">
            <circle cx="6.5" cy="6.5" r="6.5" fill="#25A796"/>
            <circle cx="6.5" cy="6.5" r="3.5" stroke="#1e1c1d" stroke-width="1" fill="none"/>
          </svg>
          www.satchelandsundial.example
        </li>
      </ul>
    </div>
    <div class="tagline-band">
      <p class="tagline">Live a life you don't need a holiday from</p>
    </div>
  </section>

  <section class="card card--back" aria-label="Business card back">
    <div class="social" aria-label="Social profiles">
      <span></span><span></span><span></span>
    </div>
    <div class="back__logo">
      <p class="wordmark wordmark--light">Satchel &amp; Sundial</p>
    </div>
  </section>
</body>
</html>
```